Basic business card

use my newly created logo - and the phrases (Lower Cost of Test & Accelarated New Product Introduction) - and my new email domain / ID - use at conferences / tradeshows

Industry/Entity Type

semiconductor

Contact Information for Business Card

Daniel K Forde, Owner, communicate via Logo - Lower COT - Cost of Test, Accelerated NPI - New Product Introduction, phone +1 555 613 0946, Chandler, Arizona, USA, daniel.forde@qal-vub.com

Font styles to use
Sans Serif

Requirements
Nice to have
• re-use my logo created via Pixel Harbor last August (#7315926)

```html
<!DOCTYPE html>
<html lang="en">
<head>
<meta charset="utf-8">
<title>QAL-VUB Business Card</title>
<link rel="stylesheet" href="https://fonts.googleapis.com/css2?family=Open+Sans:wght@400;600;700&display=swap">
<style>
  :root {
    --bg: #333333;
    --card: #1f1f21;
    --card-edge: #161617;
    --brand: #4b5671;
    --brand-light: #aab3c2;
    --orange: #f4981f;
    --cyan: #2bb3e6;
    --white: #ffffff;
  }
  * { margin: 0; padding: 0; box-sizing: border-box; }
  html, body {
    width: 1200px; height: 780px; overflow: hidden;
    background: var(--bg);
    font-family: "Open Sans", Arial, sans-serif;
  }
  .stage {
    width: 1200px; height: 780px;
    display: flex; align-items: center; justify-content: center; gap: 30px;
  }
  .card {
    position: relative;
    width: 560px; height: 320px;
    background: var(--card);
    overflow: hidden;
    box-shadow: 0 12px 30px rgba(0,0,0,.45);
  }

  /* Back side */
  .card-back__pattern {
    position: absolute; inset: 0;
    background: radial-gradient(ellipse at center, #262628 0%, #1c1c1e 70%, #18181a 100%);
  }
  .card-back__brand {
    position: absolute; left: 0; right: 0; top: 50%;
    transform: translateY(-50%);
    text-align: center;
    font-weight: 600; font-size: 58px; letter-spacing: 3px;
    color: var(--brand-light);
  }

  /* Front side */
  .brand {
    position: absolute; left: 150px; top: 44px;
    display: flex; align-items: center; gap: 14px;
  }
  .brand__mark {
    width: 26px; height: 26px; background: var(--brand);
  }
  .brand__name {
    font-weight: 600; font-size: 46px; letter-spacing: 2px;
    color: var(--brand);
  }
  .person {
    position: absolute; left: 54px; top: 160px;
  }
  .person__name {
    font-weight: 700; font-size: 28px; line-height: 1.1;
  }
  .person__first { color: var(--orange); }
  .person__last { color: var(--cyan); }
  .person__role {
    margin-top: 4px; margin-left: 60px;
    font-size: 15px; font-weight: 600; color: var(--white); letter-spacing: .5px;
  }
  .divider {
    position: absolute; left: 300px; top: 140px;
    width: 1px; height: 92px; background: #cfcfcf;
  }
  .contacts {
    position: absolute; left: 318px; top: 146px;
    list-style: none;
  }
  .contacts__item {
    display: flex; align-items: center; gap: 9px;
    font-size: 14px; color: var(--white); line-height: 26px; letter-spacing: .3px;
  }
  .contacts__icon { width: 14px; height: 14px; flex: none; }
  .address-band {
    position: absolute; left: 0; right: 0; top: 258px; height: 30px;
    background: var(--orange);
    display: flex; align-items: center; justify-content: center;
    font-size: 15px; font-weight: 600; color: var(--white); letter-spacing: .5px;
  }
</style>
</head>
<body>
<main class="stage">
  <section class="card card-back" aria-label="Card back">
    <div class="card-back__pattern" role="img" aria-label="Embossed repeating pattern of small rising-chart marks"></div>
    <div class="card-back__brand">QAL-VUB</div>
  </section>

  <section class="card card-front" aria-label="Card front">
    <div class="brand">
      <span class="brand__mark"></span>
      <span class="brand__name">QAL-VUB</span>
    </div>

    <div class="person">
      <p class="person__name"><span class="person__first">Lena</span> <span class="person__last">Marsh</span></p>
      <p class="person__role">Managing Director</p>
    </div>

    <div class="divider"></div>

    <ul class="contacts">
      <li class="contacts__item">
        <svg class="contacts__icon" viewBox="0 0 24 24" aria-hidden="true"><path fill="#f4981f" d="M6.6 10.8a15 15 0 0 0 6.6 6.6l2.2-2.2a1 1 0 0 1 1-.25 11.4 11.4 0 0 0 3.6.57 1 1 0 0 1 1 1V20a1 1 0 0 1-1 1A17 17 0 0 1 3 4a1 1 0 0 1 1-1h3.5a1 1 0 0 1 1 1c0 1.25.2 2.45.57 3.57a1 1 0 0 1-.25 1z"/></svg>
        (555) 214-0387
      </li>
      <li class="contacts__item">
        <svg class="contacts__icon" viewBox="0 0 24 24" aria-hidden="true"><rect x="2" y="5" width="20" height="14" rx="2" fill="#f4981f"/><path d="M3 6l9 7 9-7" stroke="#1f1f21" stroke-width="2" fill="none"/></svg>
        hello@qal-vub.com
      </li>
      <li class="contacts__item">
        <svg class="contacts__icon" viewBox="0 0 24 24" aria-hidden="true"><circle cx="12" cy="12" r="10" fill="#f4981f"/><path d="M2 12h20M12 2c3 3 3 17 0 20M12 2c-3 3-3 17 0 20" stroke="#1f1f21" stroke-width="1.5" fill="none"/></svg>
        www.qal-vub.com
      </li>
    </ul>

    <div class="address-band">2840 Orchard Way #210, Chandler, AZ 85226, USA</div>
  </section>
</main>
</body>
</html>
```